Harvest Lantern Jamboree Announcement on a 6x9 Postcard

I would like a 6x9 postcard mailer inviting people to our Harvest Lantern Jamboree at Cedarlight Church in Milwaukee Wisconsin. The template is included

Some activities would include:
School Supply Giveaway
Free Food
Bounce Houses
Face Painting
and more....

Date/Time: Saturday August 17th from 2pm to 4pm

Side 2 would have our Logo (We do have the AI or EPS file if needed), Date, Name, Address, QR Code, phone, Website Information.
Saturday, August 17 from 2pm-4pm
Cedarlight Church
4815 W. 37th Street
Milwaukee, WI 53288
Ph: 414-555-0172
Website: www.cedarlightfc.example
tagline: A Home Where Welcomed Friends Welcome Friends

Target Market(s)

Neighborhoods immediately surrounding our church who have young children in need of school supplies.

Industry/Entity Type

Christian Church

Colors
0054AA
0677BA
7BADD7
CADEEF
E8F1F8
EB3D1F
EC4F4E
F09395
F8D3D4
FCEDEE

Requirements
Nice to have
• I would like to have a picture of our building with additional pictures on the back side with some of the activities we will have.

```html
<!DOCTYPE html>
<html lang="en">
<head>
<meta charset="utf-8">
<title>Harvest Lantern Jamboree Postcard</title>
<link href="https://fonts.googleapis.com/css2?family=Oswald:wght@300;400;700&family=Poppins:wght@400;500;600;700;800&family=Great+Vibes&display=swap" rel="stylesheet">
<style>
:root{
  --stage:#dcdcdc;
  --navy-deep:#160f4a;
  --navy:#221673;
  --violet:#3a24a8;
  --red:#ec2a3a;
  --white:#ffffff;
  --silver:#b9b9c4;
}
*{margin:0;padding:0;box-sizing:border-box}
html,body{width:804px;height:1200px;overflow:hidden;background:var(--stage)}
body{position:relative;font-family:'Poppins',sans-serif;color:var(--white)}
.card{position:absolute;width:650px;height:434px;overflow:hidden}
.card-front{left:78px;top:149px;background:radial-gradient(ellipse at 60% 60%,var(--violet) 0%,var(--navy) 45%,var(--navy-deep) 100%)}
.card-back{left:77px;top:618px;background:var(--white)}
.abs{position:absolute}
.script{font-family:'Great Vibes',cursive;color:var(--red);white-space:nowrap}
.chrome{background:linear-gradient(180deg,#fff 0%,#fff 50%,var(--silver) 52%,#f2f2f2 100%);-webkit-background-clip:text;background-clip:text;color:transparent}
.headline{font-family:'Oswald',sans-serif;line-height:1;white-space:nowrap;text-transform:uppercase}
.headline-tall{transform-origin:left top;transform:scaleY(1.7)}
.date-box{border:1.5px solid var(--white)}
.date-day{font-family:'Oswald',sans-serif;font-weight:700;line-height:1;letter-spacing:-.5px}
.date-month{font-family:'Oswald',sans-serif;font-weight:300;line-height:1}
.date-year{background:var(--red);font-family:'Poppins',sans-serif;font-weight:500;text-align:center;letter-spacing:.55em;text-indent:.55em;line-height:1}
.date-weekday{font-family:'Poppins',sans-serif;font-weight:700;writing-mode:vertical-rl;transform:rotate(180deg);letter-spacing:.03em;line-height:1}
.time{font-weight:700;white-space:nowrap}
.to-dot{display:inline-flex;align-items:center;justify-content:center;background:var(--red);border-radius:50%;font-weight:700;vertical-align:middle}
.activities-tag{background:var(--red);font-weight:700;font-size:9px;letter-spacing:.14em;padding:2px 8px;clip-path:polygon(0 0,94% 0,100% 100%,0 100%)}
.activity-photo{border-radius:50%;border:2px solid var(--white);width:57px;height:57px}
.activity-label{font-size:8.5px;text-align:center;line-height:1.25;width:80px}
.divider-v{border-left:1px dashed rgba(255,255,255,.6);width:0}
.contact-label{color:var(--red);font-weight:700;font-size:12px;white-space:nowrap}
.contact-label span{font-weight:400}
.contact-item{font-size:10px;font-weight:500;display:flex;align-items:center;gap:4px;white-space:nowrap}
.brand-name{font-family:'Poppins',sans-serif;font-weight:700;color:var(--navy);white-space:nowrap;display:flex;align-items:center;gap:6px}
.brand-mark{display:inline-block;background:var(--red)}
.photo{border:1.5px solid var(--red)}
.button{background:var(--red);border-radius:3px;font-weight:700;font-size:15px;text-align:center;line-height:23px}
.button span{font-weight:400}
</style>
</head>
<body>

<!-- FRONT -->
<section class="card card-front">
  <div class="abs script" style="left:24px;top:22px;font-size:27px;">You are Invited to</div>
  <div class="abs headline chrome" style="left:32px;top:57px;font-size:32px;font-weight:300;">Our Harvest</div>
  <div class="abs headline chrome" style="left:31px;top:95px;font-size:44px;font-weight:700;">Lantern</div>
  <div class="abs headline chrome headline-tall" style="left:31px;top:146px;font-size:40px;font-weight:700;letter-spacing:-.5px;">Jamboree</div>

  <div class="abs date-box" style="left:228px;top:35px;width:117px;height:125px;">
    <div class="abs date-day" style="left:8px;top:13px;font-size:42px;">17TH</div>
    <div class="abs date-month" style="left:9px;top:58px;font-size:25px;">AUGUST</div>
    <div class="abs date-year" style="left:8px;top:89px;width:76px;height:20px;font-size:16px;line-height:20px;">2024</div>
    <div class="abs date-weekday" style="left:91px;top:12px;height:98px;font-size:15px;text-align:center;">SATURDAY</div>
  </div>

  <div class="abs time" style="left:227px;top:172px;font-size:18px;">2PM <span class="to-dot" style="width:22px;height:22px;font-size:12px;margin:0 4px;">to</span> 4PM</div>
  <svg class="abs" style="left:226px;top:202px" width="16" height="22" viewBox="0 0 16 22" aria-hidden="true"><path d="M8 0C3.6 0 0 3.5 0 7.8 0 13.5 8 22 8 22s8-8.5 8-14.2C16 3.5 12.4 0 8 0z" fill="var(--red)"/><circle cx="8" cy="7.8" r="3" fill="var(--navy)"/></svg>
  <div class="abs" style="left:248px;top:202px;font-size:11.5px;font-weight:500;line-height:1.2;">Cedarlight Church in<br>Milwaukee</div>

  <div class="abs activities-tag" style="left:31px;top:255px;width:172px;">SOME ACTIVITIES INCLUDE</div>
  <div class="abs" style="left:190px;top:268px;width:156px;height:1px;background:var(--red)"></div>

  <div class="abs activity-photo" role="img" aria-label="Photo of a backpack filled with school supplies" style="left:34px;top:285px;background:radial-gradient(circle,#2f63c9,#1b3d86);"></div>
  <div class="abs activity-photo" role="img" aria-label="Photo of a child in a colorful bounce house" style="left:117px;top:285px;background:radial-gradient(circle,#e9a13a,#d2412c 55%,#2a7fc7);"></div>
  <div class="abs activity-photo" role="img" aria-label="Photo of people sharing food at an outdoor table" style="left:200px;top:285px;background:radial-gradient(circle,#c9a68a,#5c6b4a);"></div>
  <div class="abs activity-photo" role="img" aria-label="Photo of a child with face paint" style="left:286px;top:285px;background:radial-gradient(circle,#f2c7a0,#d9a03c 60%,#6b8f3c);"></div>

  <div class="abs divider-v" style="left:105px;top:282px;height:90px;"></div>
  <div class="abs divider-v" style="left:188px;top:282px;height:90px;"></div>
  <div class="abs divider-v" style="left:271px;top:282px;height:90px;"></div>

  <div class="abs activity-label" style="left:23px;top:352px;">School Supply<br>Giveaway</div>
  <div class="abs activity-label" style="left:106px;top:352px;">Bounce<br>Houses</div>
  <div class="abs activity-label" style="left:189px;top:352px;">Free<br>Food</div>
  <div class="abs activity-label" style="left:275px;top:352px;">Face Painting<br>and more....</div>

  <div class="abs contact-label" style="left:30px;top:388px;">CONTACT <span>US</span></div>
  <div class="abs contact-item" style="left:117px;top:390px;">
    <svg width="10" height="10" viewBox="0 0 10 10" aria-hidden="true"><circle cx="5" cy="5" r="4.5" fill="none" stroke="var(--red)" stroke-width="1.2"/><path d="M3.3 2.8l1 1-.5.7c.3.6.8 1.1 1.4 1.4l.7-.5 1 1-.6.8C4.7 7 3 5.3 2.6 3.4z" fill="var(--red)"/></svg>414-555-0172</div>
  <div class="abs contact-item" style="left:205px;top:390px;">
    <svg width="10" height="10" viewBox="0 0 10 10" aria-hidden="true"><circle cx="5" cy="5" r="4.4" fill="none" stroke="var(--red)" stroke-width="1"/><ellipse cx="5" cy="5" rx="2" ry="4.4" fill="none" stroke="var(--red)" stroke-width=".8"/><path d="M.6 5h8.8" stroke="var(--red)" stroke-width=".8"/></svg>www.cedarlightfc.example</div>

  <svg class="abs" style="left:0;top:0" width="650" height="434" viewBox="0 0 650 434">
    <defs>
      <linearGradient id="photoFade" x1="0" y1="0" x2="0" y2="1">
        <stop offset="0" stop-color="#ffffff"/>
        <stop offset=".28" stop-color="#ffffff"/>
        <stop offset=".5" stop-color="#bdbdbd"/>
        <stop offset="1" stop-color="#5f5f5f"/>
      </linearGradient>
    </defs>
    <polygon role="img" aria-label="Black and white photo of four children stacking hands together" fill="url(#photoFade)"
      points="394,0 650,0 650,434 371,434 380,420 374,405 384,392 376,378 387,360 380,345 392,330 383,312 395,296 388,280 399,262 390,248 400,232 393,214 404,198 396,182 404,166 397,150 407,134 398,118 405,100 396,86 404,70 395,54 403,38 394,22 400,10"/>
  </svg>
  <div class="abs brand-name" style="left:452px;top:55px;font-size:26px;">
    <span class="brand-mark" style="width:16px;height:16px;"></span>CEDARLIGHT
  </div>
</section>

<!-- BACK -->
<section class="card card-back">
  <svg class="abs" style="left:0;top:0" width="650" height="434" viewBox="0 0 650 434" aria-hidden="true">
    <defs>
      <radialGradient id="backNavy" cx=".45" cy=".5" r=".7">
        <stop offset="0" stop-color="#3a24a8"/>
        <stop offset=".5" stop-color="#221673"/>
        <stop offset="1" stop-color="#160f4a"/>
      </radialGradient>
    </defs>
    <polygon fill="url(#backNavy)" points="0,0 541,0 541,226 431,226 431,379 286,379 286,434 0,434"/>
  </svg>

  <div class="abs script" style="left:31px;top:24px;font-size:34px;">A Home Where</div>
  <div class="abs headline chrome" style="left:28px;top:66px;font-family:'Poppins',sans-serif;font-weight:800;font-size:24.5px;letter-spacing:-.3px;">Welcomed Friends</div>
  <div class="abs headline chrome" style="left:28px;top:98px;font-family:'Poppins',sans-serif;font-weight:800;font-size:24.5px;letter-spacing:-.3px;">Welcome Friends</div>
  <div class="abs" style="left:26px;top:137px;font-size:10.5px;letter-spacing:.24em;font-weight:500;white-space:nowrap;">CEDARLIGHT CHURCH IN MILWAUKEE</div>

  <div class="abs date-box" style="left:291px;top:29px;width:113px;height:121px;">
    <div class="abs date-day" style="left:8px;top:12px;font-size:41px;">17TH</div>
    <div class="abs date-month" style="left:9px;top:56px;font-size:24px;">AUGUST</div>
    <div class="abs date-year" style="left:8px;top:86px;width:73px;height:20px;font-size:15.5px;line-height:20px;">2024</div>
    <div class="abs date-weekday" style="left:88px;top:11px;height:96px;font-size:14.5px;text-align:center;">SATURDAY</div>
  </div>

  <div class="abs time" style="left:433px;top:37px;width:80px;text-align:center;font-size:32px;line-height:1;">2PM</div>
  <div class="abs to-dot" style="left:454px;top:77px;width:38px;height:38px;font-size:19px;">to</div>
  <div class="abs time" style="left:433px;top:118px;width:80px;text-align:center;font-size:32px;line-height:1;">4PM</div>

  <div class="abs photo" role="img" aria-label="Photo of the church building with white columns" style="left:30px;top:171px;width:121px;height:113px;background:linear-gradient(180deg,#d8dde2 0%,#b8a394 45%,#7f5a43 60%,#5f8a3a 80%,#4d7531 100%);"></div>
  <div class="abs photo" role="img" aria-label="Photo of a child on an inflatable bounce slide" style="left:159px;top:171px;width:120px;height:113px;background:linear-gradient(160deg,#4f8a3a 0%,#7aa84a 35%,#e4473a 55%,#2f8fd0 75%,#f2c23c 100%);"></div>
  <div class="abs photo" role="img" aria-label="Photo of children reading books on the grass" style="left:286px;top:171px;width:121px;height:113px;background:linear-gradient(180deg,#6f9a3a 0%,#d9a9b5 40%,#8fb4d8 60%,#5f8f2f 100%);"></div>

  <div class="abs button" style="left:30px;top:307px;width:178px;height:23px;">CONTACT <span>US NOW</span></div>

  <div class="abs contact-item" style="left:30px;top:345px;font-size:11px;">
    <svg width="10" height="10" viewBox="0 0 10 10" aria-hidden="true"><path d="M2 .6l2 2-1 1.3c.6 1.3 1.7 2.4 3 3l1.3-1 2 2-1.2 1.5C4.7 9.3.7 5.3.5 1.8z" fill="var(--red)"/></svg>414-555-0172</div>
  <div class="abs contact-item" style="left:30px;top:365px;font-size:11px;">
    <svg width="10" height="10" viewBox="0 0 10 10" aria-hidden="true"><circle cx="5" cy="5" r="4.4" fill="none" stroke="var(--red)" stroke-width="1"/><ellipse cx="5" cy="5" rx="2" ry="4.4" fill="none" stroke="var(--red)" stroke-width=".8"/><path d="M.6 5h8.8" stroke="var(--red)" stroke-width=".8"/></svg>www.cedarlightfc.example</div>
  <div class="abs contact-item" style="left:30px;top:385px;font-size:11px;">
    <svg width="10" height="10" viewBox="0 0 10 12" aria-hidden="true"><path d="M5 0C2.2 0 0 2.1 0 4.8 0 8.3 5 12 5 12s5-3.7 5-7.2C10 2.1 7.8 0 5 0z" fill="var(--red)"/><circle cx="5" cy="4.8" r="1.8" fill="var(--navy)"/></svg>4815 W. 37th Street Milwaukee, WI 53288</div>

  <div class="abs brand-name" style="left:292px;top:324px;font-size:16px;color:var(--white);">
    <span class="brand-mark" style="width:11px;height:11px;"></span>CEDARLIGHT
  </div>
</section>

</body>
</html>
```